Executive recruiting firm in need of business card design

Executive recruiting firm looking for a sleek, classy and modern business card design; card itself will be square shape, rounded edges and soft touch paper, our colors are dark blues in the navy color scale, silvers and grays. Reference our website for a better idea of our company's feel and goals at Tarvex-Up.com - our company message is "Employee Engagement Begins at Recruitment" this should be on the card

```html
<!DOCTYPE html>
<html lang="en">
<head>
<meta charset="utf-8">
<title>Tarvex Up Business Card</title>
<link href="https://fonts.googleapis.com/css2?family=Roboto:wght@400;500;700&display=swap" rel="stylesheet">
<style>
  :root {
    --navy: #141848;
    --ink: #3a3a40;
    --paper: #f7f7f5;
    --backdrop: #e4ddd4;
  }
  * { box-sizing: border-box; margin: 0; padding: 0; }
  html, body { width: 1200px; height: 794px; overflow: hidden; }
  body {
    background: var(--backdrop);
    font-family: "Roboto", Arial, sans-serif;
    position: relative;
  }
  .card {
    position: absolute;
    top: 242px;
    width: 540px;
    height: 310px;
    background: var(--paper);
    border-radius: 6px;
    box-shadow: 0 2px 6px rgba(0,0,0,0.12);
    overflow: hidden;
  }
  .card-front { left: 40px; }
  .card-back { left: 620px; }

  .brand {
    position: absolute;
    display: flex;
    align-items: center;
    gap: 10px;
  }
  .brand-name {
    color: var(--navy);
    font-weight: 500;
    line-height: 1;
    white-space: nowrap;
  }
  .brand-mark {
    background: var(--navy);
    flex: none;
  }

  .card-front .brand { left: 0; right: 0; top: 112px; justify-content: center; }
  .card-front .brand-name { font-size: 38px; }
  .card-front .brand-mark { width: 16px; height: 16px; }
  .slogan {
    position: absolute;
    left: 0; right: 0;
    top: 238px;
    text-align: center;
    font-size: 14px;
    color: var(--ink);
    letter-spacing: 0.3px;
  }

  .person { position: absolute; left: 50px; top: 42px; }
  .person-name { font-size: 18px; font-weight: 700; color: var(--navy); }
  .person-role { font-size: 14px; font-weight: 500; color: var(--ink); margin-top: 2px; }
  .address {
    position: absolute; left: 46px; top: 150px;
    font-size: 14px; color: var(--ink); line-height: 1.3;
  }
  .contacts {
    position: absolute; left: 46px; top: 196px;
    list-style: none; font-size: 14px; color: var(--ink);
  }
  .contacts li { display: flex; align-items: center; gap: 8px; height: 18px; }
  .contacts svg { width: 12px; height: 12px; fill: var(--navy); flex: none; }

  .card-back .brand { right: 40px; top: 150px; }
  .card-back .brand-name { font-size: 26px; }
  .card-back .brand-mark { width: 12px; height: 12px; }
</style>
</head>
<body>
  <section class="card card-front">
    <div class="brand">
      <span class="brand-name">Tarvex Up</span>
      <span class="brand-mark"></span>
    </div>
    <p class="slogan">Employee Engagement Begins at Recruitment</p>
  </section>

  <section class="card card-back">
    <div class="person">
      <p class="person-name">DANIEL REYES</p>
      <p class="person-role">CEO/FOUNDER</p>
    </div>
    <p class="address">482 Linden Park Ave.<br>Marlow, CA</p>
    <ul class="contacts">
      <li><svg viewBox="0 0 12 12"><path d="M2 1l2 0 1 3-1.5 1a6 6 0 0 0 3.5 3.5L8 7l3 1v2a1 1 0 0 1-1 1A9 9 0 0 1 1 2a1 1 0 0 1 1-1z"/></svg>555 214 7730</li>
      <li><svg viewBox="0 0 12 12"><path d="M3 0h6a1 1 0 0 1 1 1v10a1 1 0 0 1-1 1H3a1 1 0 0 1-1-1V1a1 1 0 0 1 1-1zm0 1.5v8h6v-8z"/></svg>555 398 1642</li>
      <li><svg viewBox="0 0 12 12"><path d="M3 0h6v3H3zM1 4h10v5H9v3H3V9H1zm3 4v3h4V8z"/></svg>555 760 4185</li>
      <li><svg viewBox="0 0 12 12"><path d="M0 2h12v8H0zm1 1v.4l5 3.3 5-3.3V3z"/></svg>daniel@tarvex-up.com</li>
      <li><svg viewBox="0 0 12 12"><circle cx="6" cy="6" r="6"/></svg>www.tarvex-up.com</li>
    </ul>
    <div class="brand">
      <span class="brand-name">Tarvex Up</span>
      <span class="brand-mark"></span>
    </div>
  </section>
</body>
</html>
```